Website Quibrel Outdoor

Hi I'm looking for a simple design for a new website. It's outdoor products mainly in category, Boat, Tarpaulin, Fishing, Golf. I have include image and text for 8 products + presentation etc. I want a simple and modern site + fast + Mobile. Wordpress. I'm going to sell through Tradovik so I don't need any WooCommerce but a buy button to Tradovik. I haven set up the Tradovik account yet. My logo i s grey and orange. My goal is to sell in Tradovik US and later EU.

```html
<!DOCTYPE html>
<html lang="en">
<head>
<meta charset="utf-8">
<title>Quibrel Outdoor</title>
<link rel="stylesheet" href="https://fonts.googleapis.com/css2?family=Montserrat:wght@300;400;500;600;700;800&family=Roboto:ital,wght@0,400;0,500;0,700;1,400&display=swap">
<style>
:root{
  --orange:#f5821f;
  --orange-dark:#e2701a;
  --ink:#2b2b2b;
  --text:#555;
  --muted:#8a8a8a;
  --line:#d9d9d9;
  --soft:#f3f3f3;
  --dark:#2a2a2a;
  --footer:#252525;
  --topbar:#5b5b5b;
  --white:#fff;
}
*{box-sizing:border-box;margin:0;padding:0}
html,body{width:1200px;height:4975px;overflow:hidden}
body{font-family:'Roboto',Arial,sans-serif;color:var(--text);background:var(--white);position:relative}
section,header,footer,.topbar{position:absolute;left:0;width:1200px}
.abs{position:absolute}
a{color:inherit;text-decoration:none}

.topbar{top:0;height:35px;background:var(--topbar);color:#eee;font-size:13px;text-align:center;line-height:35px}

.site-header{top:35px;height:149px;background:var(--white)}
.brand{left:110px;top:18px;width:150px;text-align:center}
.brand-dot{width:56px;height:56px;border-radius:50%;background:#6b6b6b;margin:0 auto 6px}
.brand-name{font-family:'Montserrat',sans-serif;font-weight:700;color:var(--orange);font-size:21px;line-height:22px;letter-spacing:1px;text-transform:uppercase}
.contact-row{right:114px;top:33px;display:flex;gap:30px;font-size:14px;color:#444;align-items:center}
.contact-row span{display:flex;align-items:center;gap:6px}
.nav{right:114px;top:97px;display:flex;gap:33px;font-size:15px;color:#444}

.hero{top:184px;height:687px;overflow:hidden}
.hero-photo{position:absolute;inset:0;background:linear-gradient(180deg,#4a3322 0%,#a85d22 22%,#e99535 38%,#d27a2a 52%,#6b3f1f 68%,#2e1e14 100%)}
.hero-title{top:60px;left:0;width:1200px;text-align:center;font-family:'Montserrat',sans-serif;font-weight:700;font-size:84px;color:var(--white);letter-spacing:1px}
.hero-sub{top:170px;left:0;width:1200px;text-align:center;color:var(--white);font-size:16px;line-height:29px}
.btn{display:inline-block;background:var(--orange);color:var(--white);font-family:'Montserrat',sans-serif;font-weight:600;border-radius:30px}
.hero-btn{top:239px;left:466px;width:220px;height:56px;line-height:56px;text-align:center;font-size:17px;box-shadow:4px 4px 0 -1px var(--orange-dark)}
.slider-count{left:1128px;color:#ddd;font-size:15px}
.slider-line{left:1138px;top:212px;width:2px;height:212px;background:rgba(255,255,255,.5)}
.slider-line::after{content:"";position:absolute;left:0;top:0;width:2px;height:70px;background:var(--white)}
.hero-dashes{top:649px;left:522px;display:flex;gap:10px}
.hero-dashes i{display:block;width:32px;height:4px;background:rgba(255,255,255,.9)}

.sec-title{left:0;width:1200px;text-align:center;font-family:'Montserrat',sans-serif;font-size:42px;color:var(--ink)}
.sec-title .light{font-weight:300}
.sec-title .bold{font-weight:800}
.sec-title .o{color:var(--orange)}

.category{top:871px;height:582px;background:var(--soft)}
.cat-card{top:166px;width:302px;height:327px;border:1px solid #bdbdbd;background:var(--soft);padding:0 16px}
.cat-icon{width:108px;height:108px;border-radius:50%;background:var(--orange);margin:20px auto 0}
.cat-card h3{font-family:'Montserrat',sans-serif;font-weight:500;font-size:23px;color:var(--ink);margin-top:22px}
.cat-card p{font-size:12.5px;line-height:25px;color:#666;margin-top:8px}
.arrow{width:34px;height:34px;top:310px}

.products{top:1453px;height:657px;background:var(--white)}
.prod-card{top:164px;width:233px;height:323px;background:var(--white);box-shadow:0 0 6px rgba(0,0,0,.18)}
.prod-img{position:absolute;left:14px;top:8px;width:205px;height:200px;background:linear-gradient(180deg,#f4f4f4,#dcdcdc)}
.prod-name{position:absolute;left:14px;top:220px;width:150px;font-size:16px;line-height:24px;color:#444}
.cart{position:absolute;right:14px;top:222px;width:44px;height:44px;border-radius:50%;background:var(--orange);display:flex;align-items:center;justify-content:center}
.price{position:absolute;left:14px;top:284px;color:var(--orange);font-size:17px;font-weight:500}
.dots{display:flex;gap:5px}
.dots i{display:block;width:12px;height:12px;border-radius:50%;border:1.5px solid #333}
.dots i.on{background:var(--orange);border-color:var(--orange)}
.dots i.ring{border-color:var(--orange)}

.feature{top:2110px;height:560px;background:var(--dark)}
.feature-img{left:663px;top:-41px;width:512px;height:570px;background:linear-gradient(160deg,#f79a3e 0%,#f5821f 55%,#e2701a 100%)}
.feature-title{left:110px;top:66px;font-family:'Montserrat',sans-serif;font-size:31px;color:var(--white)}
.feature-title b{color:var(--orange);font-weight:800}
.feature-title span{font-weight:400}
.f-point{left:110px;width:520px;padding-left:26px;color:var(--white);font-size:13px;line-height:25px}
.f-point svg{position:absolute;left:0;top:5px}
.f-tick{left:144px;color:var(--white);font-size:14.5px;padding-left:24px}
.f-tick svg{position:absolute;left:0;top:2px}
.thumb{top:421px;width:100px;height:82px;border-radius:10px}

.testimonials{top:2670px;height:643px;background:var(--white)}
.t-card{top:164px;width:261px;height:354px;background:var(--white);box-shadow:0 0 8px rgba(0,0,0,.2);padding:0 24px}
.t-card svg{margin-top:38px}
.t-card p{font-style:italic;font-size:12.5px;line-height:25px;color:#666;margin-top:20px}
.t-author{display:flex;align-items:center;gap:10px;margin-top:20px;color:var(--orange);font-size:15px}
.avatar{width:52px;height:52px;border-radius:50%;background:linear-gradient(135deg,#c7a27c,#7d5b43)}

.loving{top:3313px;height:599px;background:var(--soft)}
.love-item{top:170px;width:302px;text-align:center}
.love-img{width:302px;height:242px}
.love-item h4{font-size:15.5px;font-weight:700;color:#333;margin-top:28px}
.love-item p{font-size:13px;line-height:25px;color:#555;margin-top:10px}

.contact{top:3912px;height:520px;background:var(--white)}
.contact-title{left:110px;top:150px;font-family:'Montserrat',sans-serif;font-size:42px;color:var(--ink)}
.contact-title .light{font-weight:300;color:var(--orange)}
.contact-title .bold{font-weight:800}
.contact-text{left:110px;top:222px;width:430px;font-size:12.5px;line-height:26px;color:#666}
.contact-link{left:112px;top:346px;color:var(--orange);font-size:15px;text-decoration:underline}
.field{left:624px;width:491px;border-bottom:1.5px solid #bbb;font-size:13px;color:#333;padding-bottom:14px}
.submit{left:624px;top:371px;width:226px;height:54px;line-height:54px;text-align:center;font-size:20px;font-weight:700;box-shadow:4px 4px 0 -1px #444}

.site-footer{top:4432px;height:543px;background:var(--footer);color:#ddd}
.newsletter{left:108px;top:68px;font-family:'Montserrat',sans-serif;font-size:23px;color:var(--white)}
.newsletter b{font-weight:800}
.newsletter span{font-weight:300;color:var(--orange)}
.nl-input{left:529px;top:63px;width:360px;height:42px;border-radius:22px;background:var(--white);font-size:12px;color:#333;line-height:42px;padding-left:18px}
.nl-btn{left:900px;top:63px;width:188px;height:42px;line-height:42px;text-align:center;font-size:15px;font-weight:700;border-radius:22px}
.f-rule{left:110px;width:978px;height:1px;background:#555}
.f-brand{left:110px;top:186px;width:170px;text-align:center}
.cards{left:112px;top:355px;display:flex;gap:4px;padding:5px;background:var(--white);border-radius:3px}
.cards i{display:block;width:36px;height:28px;border-radius:3px;background:#cfd6e6}
.f-col{top:205px;font-size:13px;color:#ddd}
.f-col h5{font-size:15px;font-weight:700;color:var(--white);margin-bottom:12px;letter-spacing:.5px}
.f-col li{list-style:none;line-height:31.7px}
.copy{top:485px;left:0;width:1200px;text-align:center;font-size:13px;color:#ddd}
</style>
</head>
<body>

<div class="topbar">Lorem ipsum dolor sit amet, consectetur adipiscing elit, sed</div>

<header class="site-header">
  <div class="abs brand">
    <div class="brand-dot"></div>
    <div class="brand-name">Quibrel<br>Outdoor</div>
  </div>
  <div class="abs contact-row">
    <span><svg width="13" height="13" viewBox="0 0 24 24"><path fill="#f5821f" d="M6.6 10.8a15 15 0 0 0 6.6 6.6l2.2-2.2c.3-.3.7-.4 1-.2 1.1.4 2.300.6 3.6.6.6 0 1 .4 1 1V20c0 .6-.4 1-1 1A17 17 0 0 1 3 4c0-.6.4-1 1-1h3.5c.6 0 1 .4 1 1 0 1.3.2 2.5.6 3.6.1.3 0 .7-.2 1z"/></svg>888-888-8888</span>
    <span><svg width="14" height="11" viewBox="0 0 24 18"><rect width="24" height="18" rx="2" fill="#f5821f"/><path d="M1 2l11 8 11-8" stroke="#fff" stroke-width="2" fill="none"/></svg>info@QuibrelOutdoor.com</span>
    <span style="gap:22px">
      <svg width="14" height="14" viewBox="0 0 24 24"><circle cx="10" cy="10" r="7" stroke="#333" stroke-width="3" fill="none"/><path d="M15 15l7 7" stroke="#333" stroke-width="3"/></svg>
      <svg width="15" height="14" viewBox="0 0 24 22"><path d="M0 1h4l3 12h13l3-9H6" stroke="#333" stroke-width="2.5" fill="none"/><circle cx="9" cy="19" r="2" fill="#333"/><circle cx="18" cy="19" r="2" fill="#333"/></svg>
      <span style="gap:4px"><svg width="12" height="13" viewBox="0 0 24 24"><circle cx="12" cy="7" r="6" fill="#333"/><path d="M1 24c0-7 5-10 11-10s11 3 11 10z" fill="#333"/></svg>Signup</span>
    </span>
  </div>
  <nav class="abs nav"><a>Home</a><a>About Us</a><a>Category</a><a>Products</a><a>Specification</a><a>Contact</a></nav>
</header>

<section class="hero">
  <div class="hero-photo" role="img" aria-label="Lit tent on a rocky lakeshore at sunset with a hiker looking over the water"></div>
  <h1 class="abs hero-title">Quibrel Outdoor</h1>
  <p class="abs hero-sub">The autumn storms wear hard on tarpaulins. An elastic rubber band to mount on<br>the ropes to reduce the jerk in the tarpaulin when it blows.</p>
  <a class="abs btn hero-btn">Get Started</a>
  <span class="abs slider-count" style="top:176px">01</span>
  <div class="abs slider-line"></div>
  <span class="abs slider-count" style="top:442px">04</span>
  <div class="abs hero-dashes"><i></i><i></i><i></i><i></i></div>
</section>

<section class="category">
  <h2 class="abs sec-title" style="top:76px"><span class="light o">Our</span> <span class="bold">Category</span></h2>
  <svg class="abs arrow" style="left:74px" viewBox="0 0 34 34"><circle cx="17" cy="17" r="15" fill="none" stroke="#222" stroke-width="2"/><path d="M19 11l-6 6 6 6" fill="none" stroke="#222" stroke-width="2"/></svg>
  <div class="abs cat-card" style="left:128px">
    <div class="cat-icon" role="img" aria-label="Boat icon"></div>
    <h3>Boat</h3>
    <p>Lorem ipsum dolor sit amet, adipiscing elit, sed do eiusmod tempor incididunt ut labore et dolore magna aliqua. Ut enim ad minim veniam,</p>
  </div>
  <div class="abs cat-card" style="left:448px">
    <div class="cat-icon" role="img" aria-label="Tarpaulin shelter icon"></div>
    <h3>Presenning</h3>
    <p>Lorem ipsum dolor sit amet, adipiscing elit, sed do eiusmod tempor incididunt ut labore et dolore magna aliqua. Ut enim ad minim veniam,</p>
  </div>
  <div class="abs cat-card" style="left:769px">
    <div class="cat-icon" role="img" aria-label="Tent and trees outdoor icon"></div>
    <h3>Outdoor</h3>
    <p>Lorem ipsum dolor sit amet, adipiscing elit, sed do eiusmod tempor incididunt ut labore et dolore magna aliqua. Ut enim ad minim veniam,</p>
  </div>
  <svg class="abs arrow" style="left:1090px" viewBox="0 0 34 34"><circle cx="17" cy="17" r="15" fill="none" stroke="#222" stroke-width="2"/><path d="M15 11l6 6-6 6" fill="none" stroke="#222" stroke-width="2"/></svg>
</section>

<section class="products">
  <h2 class="abs sec-title" style="top:77px"><span class="light">Our</span> <span class="bold o">Products</span></h2>
  <div class="abs prod-card" style="left:110px">
    <div class="prod-img" role="img" aria-label="Glasses hanging from a clip cord"></div>
    <div class="prod-name">Glasses in clips - hanging</div>
    <div class="cart"><svg width="16" height="15" viewBox="0 0 24 22"><path d="M0 1h4l3 12h13l3-9H6z" fill="#fff"/><circle cx="9" cy="19" r="2" fill="#fff"/><circle cx="18" cy="19" r="2" fill="#fff"/></svg></div>
    <div class="price">$120.00</div>
  </div>
  <div class="abs prod-card" style="left:359px">
    <div class="prod-img" role="img" aria-label="Clear water weight bag"></div>
    <div class="prod-name">Trapaulin weight bag</div>
    <div class="cart"><svg width="16" height="15" viewBox="0 0 24 22"><path d="M0 1h4l3 12h13l3-9H6z" fill="#fff"/><circle cx="9" cy="19" r="2" fill="#fff"/><circle cx="18" cy="19" r="2" fill="#fff"/></svg></div>
    <div class="price">$120.00</div>
  </div>
  <div class="abs prod-card" style="left:609px">
    <div class="prod-img" role="img" aria-label="Grey towel on an orange holder clip"></div>
    <div class="prod-name">Towel with holder kopiera</div>
    <div class="cart"><svg width="16" height="15" viewBox="0 0 24 22"><path d="M0 1h4l3 12h13l3-9H6z" fill="#fff"/><circle cx="9" cy="19" r="2" fill="#fff"/><circle cx="18" cy="19" r="2" fill="#fff"/></svg></div>
    <div class="price">$120.00</div>
  </div>
  <div class="abs prod-card" style="left:856px">
    <div class="prod-img" role="img" aria-label="Clip-on magnifier glasses with cord"></div>
    <div class="prod-name">Clip on nose - magnifier glasses</div>
    <div class="cart"><svg width="16" height="15" viewBox="0 0 24 22"><path d="M0 1h4l3 12h13l3-9H6z" fill="#fff"/><circle cx="9" cy="19" r="2" fill="#fff"/><circle cx="18" cy="19" r="2" fill="#fff"/></svg></div>
    <div class="price">$120.00</div>
  </div>
  <div class="abs dots" style="left:558px;top:529px"><i class="on"></i><i></i><i></i><i></i><i></i></div>
</section>

<section class="feature">
  <div class="abs feature-img" role="img" aria-label="Portable urinal bottle with funnel adapter on an orange background"></div>
  <h2 class="abs feature-title"><b>Emergency Bottle</b> <span>- Urinoar</span></h2>
  <div class="abs f-point" style="top:125px">
    <svg width="15" height="15" viewBox="0 0 16 16"><circle cx="8" cy="8" r="8" fill="#fff"/><path d="M6 4l4 4-4 4" stroke="#2a2a2a" stroke-width="2" fill="none"/></svg>
    Necessity knows no law. When you need to go, you need. On the boat it is more difficult. It sways and you easily fall into the lake. Many drowning accidents are just when you relieve the pressure.
  </div>
  <div class="abs f-point" style="top:221px">
    <svg width="15" height="15" viewBox="0 0 16 16"><circle cx="8" cy="8" r="8" fill="#fff"/><path d="M6 4l4 4-4 4" stroke="#2a2a2a" stroke-width="2" fill="none"/></svg>
    A urinal bottle can be a simple lifesaver.A potty that fits both men and women (adapter included) makes life on board more comfortable
  </div>
  <div class="abs f-tick" style="top:299px"><svg width="14" height="14" viewBox="0 0 14 14"><path d="M1 7l4 4 8-9" stroke="#f5821f" stroke-width="2.5" fill="none"/></svg>Large volume 1 liter</div>
  <div class="abs f-tick" style="top:333px"><svg width="14" height="14" viewBox="0 0 14 14"><path d="M1 7l4 4 8-9" stroke="#f5821f" stroke-width="2.5" fill="none"/></svg>Unisex - for both men and women</div>
  <div class="abs f-tick" style="top:368px"><svg width="14" height="14" viewBox="0 0 14 14"><path d="M1 7l4 4 8-9" stroke="#f5821f" stroke-width="2.5" fill="none"/></svg>Mesh storage bag for the bottle</div>
  <div class="abs thumb" style="left:110px;background:linear-gradient(160deg,#6f95c4,#1f3f6e)" role="img" aria-label="Speedboat on blue water"></div>
  <div class="abs thumb" style="left:230px;background:linear-gradient(180deg,#3a3550,#e79a3a 60%,#2b1f1a)" role="img" aria-label="Tent glowing at dusk"></div>
  <div class="abs thumb" style="left:350px;background:linear-gradient(180deg,#514a6a,#a27a8a 55%,#3a2f38)" role="img" aria-label="Boat moored at twilight"></div>
</section>

<section class="testimonials">
  <h2 class="abs sec-title" style="top:86px"><span class="light o">Client</span> <span class="bold">Testimonials</span></h2>
  <div class="abs t-card" style="left:182px">
    <svg width="40" height="26" viewBox="0 0 40 26"><path d="M2 2h15v12l-6 10H6l4-9H2zM22 2h15v12l-6 10h-5l4-9h-8z" fill="none" stroke="#f5821f" stroke-width="2"/></svg>
    <p>Lorem ipsum dolor sit amet, consectetur adipiscing elit, sed do eiusmod tempor incididunt ut labore et dolore magna aliqua. Ut enim ad minim veniam, quis nostrud exercitation ullamco laboris nisi ut aliquip</p>
    <div class="t-author"><div class="avatar" role="img" aria-label="Customer portrait"></div>Mira Tolvan</div>
  </div>
  <div class="abs t-card" style="left:470px">
    <svg width="40" height="26" viewBox="0 0 40 26"><path d="M2 2h15v12l-6 10H6l4-9H2zM22 2h15v12l-6 10h-5l4-9h-8z" fill="none" stroke="#f5821f" stroke-width="2"/></svg>
    <p>Lorem ipsum dolor sit amet, consectetur adipiscing elit, sed do eiusmod tempor incididunt ut labore et dolore magna aliqua. Ut enim ad minim veniam, quis nostrud exercitation ullamco laboris nisi ut aliquip</p>
    <div class="t-author"><div class="avatar" role="img" aria-label="Customer portrait"></div>Mira Tolvan</div>
  </div>
  <div class="abs t-card" style="left:755px">
    <svg width="40" height="26" viewBox="0 0 40 26"><path d="M2 2h15v12l-6 10H6l4-9H2zM22 2h15v12l-6 10h-5l4-9h-8z" fill="none" stroke="#f5821f" stroke-width="2"/></svg>
    <p>Lorem ipsum dolor sit amet, consectetur adipiscing elit, sed do eiusmod tempor incididunt ut labore et dolore magna aliqua. Ut enim ad minim veniam, quis nostrud exercitation ullamco laboris nisi ut aliquip</p>
    <div class="t-author"><div class="avatar" role="img" aria-label="Customer portrait"></div>Mira Tolvan</div>
  </div>
  <div class="abs dots" style="left:563px;top:546px"><i></i><i></i><i></i><i class="ring"></i><i></i></div>
</section>

<section class="loving">
  <h2 class="abs sec-title" style="top:63px"><span class="bold">What We're</span> <span class="light o">Loving</span></h2>
  <div class="abs love-item" style="left:110px">
    <div class="love-img" style="background:linear-gradient(180deg,#b8a9a3,#e4b98e 40%,#6b5a4c 65%,#3c3a2e)" role="img" aria-label="Hiker beside a tent on a hill at sunset"></div>
    <h4>Lorem ipsum dolor sit amet</h4>
    <p>Lorem ipsum dolor sit amet, adipiscing elit, sed do eiusmod tempor incididunt ut labore et dolore magna aliqua.</p>
  </div>
  <div class="abs love-item" style="left:448px">
    <div class="love-img" style="background:linear-gradient(180deg,#5e6a58,#c8622c 55%,#6f5a44)" role="img" aria-label="Angler in an orange jacket holding a fishing rod"></div>
    <h4>Lorem ipsum dolor sit amet</h4>
    <p>Lorem ipsum dolor sit amet, adipiscing elit, sed do eiusmod tempor incididunt ut labore et dolore magna aliqua.</p>
  </div>
  <div class="abs love-item" style="left:786px">
    <div class="love-img" style="background:linear-gradient(180deg,#7f9a52,#3b3b3b 50%,#5f7f3a)" role="img" aria-label="Golf bag with clubs on a green lawn"></div>
    <h4>Lorem ipsum dolor sit amet</h4>
    <p>Lorem ipsum dolor sit amet, adipiscing elit, sed do eiusmod tempor incididunt ut labore et dolore magna aliqua.</p>
  </div>
</section>

<section class="contact">
  <h2 class="abs contact-title"><span class="light">Contact</span> <span class="bold">Us Now</span></h2>
  <p class="abs contact-text">Lorem ipsum dolor sit amet, consectetur adipiscing elit, sed do eiusmod tempor incididunt ut labore et dolore magna aliqua. Ut enim ad minim veniam, quis nostrud exercitation ullamco laboris nisi ut aliquip ex ea commodo consequat.</p>
  <a class="abs contact-link">CONTACT US NOW</a>
  <div class="abs field" style="top:95px">Name</div>
  <div class="abs field" style="top:153px">Email Address</div>
  <div class="abs field" style="top:213px">Phone Number</div>
  <div class="abs field" style="top:272px;padding-bottom:60px">Message</div>
  <a class="abs btn submit">SUBMIT</a>
</section>

<footer class="site-footer">
  <h3 class="abs newsletter"><b>Subscribe to our</b> <span>Newsletter</span></h3>
  <div class="abs nl-input">Email Address</div>
  <a class="abs btn nl-btn">SUBSCRIBE</a>
  <div class="abs f-rule" style="top:151px"></div>
  <div class="abs f-brand">
    <div class="brand-dot" style="width:70px;height:70px;margin-bottom:10px"></div>
    <div class="brand-name" style="font-size:28px;line-height:32px">Quibrel<br>Outdoor</div>
  </div>
  <div class="abs cards"><i></i><i></i><i></i><i></i></div>
  <div class="abs f-col" style="left:462px">
    <h5>QUICK LINKS</h5>
    <ul><li>Home</li><li>About Us</li><li>Category</li><li>Products</li><li>Specification</li><li>Contact</li></ul>
  </div>
  <div class="abs f-col" style="left:636px">
    <h5>CONTACT</h5>
    <ul>
      <li>&#9679; Lorem ipsum dolor sit amet, consectetur</li>
      <li>adipiscing elit, sed do eiusmod</li>
      <li>&#9742; 888-888-8888</li>
      <li>&#9993; info@QuibrelOutdoor.com</li>
    </ul>
  </div>
  <div class="abs f-col" style="left:960px">
    <h5>HELP US</h5>
    <ul><li>Privacy Policy</li><li>General Information</li><li>Terms &amp; Conditions</li></ul>
  </div>
  <div class="abs f-rule" style="top:452px"></div>
  <p class="abs copy">© 2021 All Rights Reserved</p>
</footer>

</body>
</html>
```